International emerging specialist Research and Development Company focused on plant-based medicine

We need a powerpoint design for a new company based in British Columbia, Canada called Tavrel Phytocor. We are focused on developing plant-based medicines. The company is driven by its experience in research and development work in plant genetics, cultivation techniques, natural medicines, biochemistry, agriculture and technologies. Tavrel will research, develop and produce very unique and specific cultivars from the plant kingdom needed for specific ailments in medical patients. We would like to see designs that use our current logo and its colour scheme. The final design should communicate financial safety, growth, and research and development.

```html
<!DOCTYPE html>
<html lang="en">
<head>
<meta charset="utf-8">
<title>Tavrel Phytocor – Title Slide</title>
<link href="https://fonts.googleapis.com/css2?family=Roboto+Condensed:wght@300;400&display=swap" rel="stylesheet">
<style>
  :root {
    --brand-red: #d3151d;
    --paper: #efefef;
    --footer-grey: #d2d2d2;
    --ink-light: #ffffff;
    --ink-dark: #58585a;
  }
  * { margin: 0; padding: 0; box-sizing: border-box; }
  html, body {
    width: 1200px;
    height: 900px;
    overflow: hidden;
    background: var(--paper);
  }
  .slide {
    position: relative;
    width: 1200px;
    height: 900px;
    font-family: "Roboto Condensed", "Arial Narrow", sans-serif;
  }
  .hero-band {
    position: absolute;
    left: 0; top: 0;
    width: 1200px;
    height: 578px;
    background: var(--brand-red);
  }
  .hero-text {
    position: absolute;
    right: 48px;
    top: 358px;
    text-align: right;
    color: var(--ink-light);
  }
  .project-title {
    font-weight: 400;
    font-size: 51px;
    line-height: 1;
    letter-spacing: -0.3px;
  }
  .project-subtext {
    margin-top: 20px;
    font-weight: 400;
    font-size: 19px;
    line-height: 30px;
  }
  .brand-area {
    position: absolute;
    left: 0; top: 578px;
    width: 1200px;
    height: 280px;
    background: var(--paper);
  }
  .company-name {
    position: absolute;
    right: 38px;
    top: 92px;
    display: flex;
    align-items: center;
    gap: 16px;
    color: var(--ink-dark);
    font-weight: 300;
    font-size: 48px;
    line-height: 1;
  }
  .company-dot {
    width: 22px;
    height: 22px;
    border-radius: 50%;
    background: var(--brand-red);
  }
  .footer-bar {
    position: absolute;
    left: 0; bottom: 0;
    width: 1200px;
    height: 42px;
    background: var(--footer-grey);
  }
</style>
</head>
<body>
  <main class="slide">
    <section class="hero-band">
      <div class="hero-text">
        <h1 class="project-title">Project Title Here</h1>
        <p class="project-subtext">Subtext here Subtext here Subtext here<br>Subtext here Subtext here Subtext here</p>
      </div>
    </section>
    <section class="brand-area">
      <div class="company-name">
        <span class="company-dot" aria-hidden="true"></span>
        <span>Tavrel Phytocor</span>
      </div>
    </section>
    <footer class="footer-bar"></footer>
  </main>
</body>
</html>
```